Corporate Design für Hotel/Restaurant
Zielgruppe
Unsere Kundschaft ist sehr breit gestreut. Unser CI sollte entsprechend die Ü60 jährigen, wie auch die ca. 30+ jährigen Kleinstädter ansprechen.
Aufgabenstellung
Es handelt sich um einen Familienbetrieb in zweiter Generation, der trotz altem deutschen Namen „Hotel-Restaurant zum Brunnenhof“ eine klare asiatische Ausrichtung, sowohl vom Interieur, wie auch vom Speisenangebot hat.
Der rote Familienstempel soll sich auch weiterhin im Design finden (muss allerdings nicht unbedingt rot sein).
Ebenso möchten wir das Bild der Mutter aus Ihrer Jungend weiter aufgreifen.
Wir könnten uns ein ähnliches Bild auf den Tischen vorstellen, wie im Anhang zu sehen.
Wir möchten neue Speisekarten für die Abend- und Mittagskarte entwerfen lassen, die gerne mit Skizzen von koreanischem Streetfood untermalt werden sollen.
Wir stellen uns eine Bindung der Speisekarte auf einem Klemmbrett oder durch eine Holzleiste an der Seite (wie bei einem Buch) vor. Hierfür benötigen wir auch entsprechende Papiervorschläge. Wir möchten keine laminierte Speisekarte, eventuell, aber gewachstes, robustes Papier.
Auch bedruckte Tischsets könnten wir uns vorstellen, sowie im weiteren Schritt Essstäbchen mit Gravur oder Druck. Desweiteren wären Papierservietten wünschenswert.
Generell muss ein Spagat zwischen Deutsch und Asiatisch hergestellt werden.
Unsere Typografie ist festgesetzt auf SAUNA SMALL CAPS
wir interessieren uns weiterhin für Poloshirt, Sweater oder Schürzen mit dem neuen CI

```html
<!DOCTYPE html>
<html lang="de">
<head>
<meta charset="utf-8">
<title>Hotel-Restaurant zum Brunnenhof – Visitenkarte</title>
<link href="https://fonts.googleapis.com/css2?family=Alegreya+Sans+SC:wght@400;500&display=swap" rel="stylesheet">
<style>
  :root {
    --backdrop: #a89c97;
    --paper: #ebe6e3;
    --ink: #141212;
    --seal-red: #b00a0a;
    --paper-text: #f4efec;
    --rule: #6a6462;
  }
  * { box-sizing: border-box; margin: 0; padding: 0; }
  html, body { width: 857px; height: 1200px; overflow: hidden; }
  body {
    background: var(--backdrop);
    font-family: "Alegreya Sans SC", "Helvetica Neue", sans-serif;
    color: var(--ink);
    position: relative;
  }
  .card {
    position: absolute;
    left: 108px;
    width: 640px;
    height: 380px;
    background: var(--paper);
    box-shadow: 0 10px 24px rgba(40, 30, 28, 0.25);
  }
  .card--front { top: 150px; }
  .card--back { top: 660px; }

  .emblem { display: flex; gap: 10px; }
  .emblem__portrait, .emblem__seal { width: 66px; height: 82px; }

  .wordmark {
    font-weight: 400;
    text-transform: uppercase;
    line-height: 0.95;
    letter-spacing: 0.5px;
  }
  .tagline-band {
    display: inline-block;
    background: var(--seal-red);
    color: var(--paper-text);
    font-family: "Alegreya Sans SC", "Helvetica Neue", sans-serif;
    font-weight: 400;
    letter-spacing: 1.5px;
    padding: 1px 14px 3px;
    line-height: 1.1;
  }

  /* front */
  .card--front .emblem { position: absolute; left: 242px; top: 92px; }
  .card--front .brand { position: absolute; left: 0; right: 0; top: 196px; text-align: center; }
  .card--front .wordmark { font-size: 34px; }
  .card--front .tagline-band { font-size: 19px; margin-top: 8px; }

  /* back */
  .card--back .emblem { position: absolute; left: 36px; top: 36px; }
  .card--back .emblem__portrait, .card--back .emblem__seal { width: 62px; height: 78px; }
  .card--back .brand { position: absolute; left: 192px; top: 40px; }
  .card--back .wordmark { font-size: 25px; }
  .card--back .tagline-band { font-size: 16px; margin-top: 6px; }
  .card--back .divider {
    position: absolute; left: 192px; right: 36px; top: 150px;
    border-top: 1px solid var(--rule);
  }
  .contact { position: absolute; left: 192px; top: 176px; width: 300px; font-size: 15px; line-height: 1.15; letter-spacing: 0.4px; }
  .contact__address { padding-bottom: 10px; border-bottom: 1px solid var(--rule); margin-bottom: 10px; }
  .phone-band {
    position: absolute; left: 192px; top: 296px;
    background: var(--seal-red);
    color: var(--paper-text);
    font-family: "Alegreya Sans SC", "Helvetica Neue", sans-serif;
    font-size: 40px; letter-spacing: 2px;
    padding: 2px 22px;
  }
</style>
</head>
<body>

<section class="card card--front">
  <div class="emblem">
    <svg class="emblem__portrait" viewBox="0 0 66 82" role="img" aria-label="Gestempeltes Porträt der Mutter in Rot">
      <ellipse cx="33" cy="41" rx="31" ry="39" fill="var(--seal-red)"/>
    </svg>
    <svg class="emblem__seal" viewBox="0 0 66 82" role="img" aria-label="Familienstempel">
      <ellipse cx="33" cy="41" rx="30" ry="38" fill="none" stroke="var(--seal-red)" stroke-width="3"/>
    </svg>
  </div>
  <div class="brand">
    <h1 class="wordmark">Hotel-Restaurant<br>zum Brunnenhof</h1>
    <span class="tagline-band">Familienbetrieb</span>
  </div>
</section>

<section class="card card--back">
  <div class="emblem">
    <svg class="emblem__portrait" viewBox="0 0 66 82" role="img" aria-label="Gestempeltes Porträt der Mutter in Rot">
      <ellipse cx="33" cy="41" rx="31" ry="39" fill="var(--seal-red)"/>
    </svg>
    <svg class="emblem__seal" viewBox="0 0 66 82" role="img" aria-label="Familienstempel">
      <ellipse cx="33" cy="41" rx="30" ry="38" fill="none" stroke="var(--seal-red)" stroke-width="3"/>
    </svg>
  </div>
  <div class="brand">
    <h2 class="wordmark">Hotel-Restaurant<br>zum Brunnenhof</h2>
    <span class="tagline-band">Familienbetrieb</span>
  </div>
  <div class="divider"></div>
  <div class="contact">
    <p class="contact__address">Lindenweg 12,<br>31675 Bückeburg</p>
    <p class="contact__hours">Rezeption /<br>täglich besetzt von:<br>06:00 – 22:00 Uhr</p>
  </div>
  <p class="phone-band">05722 / 471-0</p>
</section>

</body>
</html>
```